i need a business card design for my family investment company "quorin investments" based in dubai. its a diverse investment firm focusing on education, hospitality and automotive. the design has to be modern and try to incorporate the logo "E" in the design. details on card as follow

Yusuf K Bin Tarrah
Managing Director
yusuf@quorin-mail.ae
www.quorin-mail.ae

Harbor district,palwick tower, office 2212, dubai
tel. 04 3850927
mobile.050 9184203

card used for networking events and investor meetings

Hospitality

```html
<!DOCTYPE html>
<html lang="en">
<head>
<meta charset="utf-8">
<title>Quorin Investments – Business Card</title>
<link href="https://fonts.googleapis.com/css2?family=Lato:wght@300;400;700&display=swap" rel="stylesheet">
<style>
  :root {
    --page: #ecebe8;
    --blue-dark: #3d6b92;
    --blue-mid: #5489b4;
    --blue-light: #6a9fc7;
    --paper-shade: #e6e6e6;
    --ink: #3a3f45;
    --white: #ffffff;
  }
  * { margin: 0; padding: 0; box-sizing: border-box; }
  html, body { width: 1200px; height: 1023px; overflow: hidden; }
  body {
    background: var(--page);
    font-family: "Lato", Arial, sans-serif;
    position: relative;
  }
  .card {
    position: absolute;
    width: 560px;
    height: 320px;
    border-radius: 22px;
    overflow: hidden;
    box-shadow: 0 10px 24px rgba(0,0,0,0.18);
  }
  /* Front */
  .card-front { left: 60px; top: 110px; background: linear-gradient(160deg, var(--white), var(--paper-shade)); }
  .front-panel { position: absolute; inset: 0; }
  .brand-lockup {
    display: flex; align-items: center; gap: 12px;
  }
  .brand-mark { width: 12px; height: 12px; background: var(--blue-mid); flex: none; }
  .brand-name {
    font-weight: 300;
    text-transform: uppercase;
    color: var(--ink);
  }
  .card-front .brand-lockup {
    position: absolute;
    left: 34px; top: 120px;
    width: 220px;
  }
  .card-front .brand-name {
    font-size: 21px;
    letter-spacing: 3px;
    line-height: 1.35;
  }
  .details {
    position: absolute;
    left: 300px; top: 34px;
    width: 236px;
    color: var(--white);
  }
  .holder-name { font-weight: 700; font-size: 19px; }
  .holder-title { font-weight: 400; font-size: 13px; margin-top: 2px; }
  .company { font-weight: 700; font-size: 13px; margin-top: 22px; }
  .address { font-size: 12.5px; line-height: 1.4; }
  .contacts { list-style: none; margin-top: 18px; }
  .contacts li { display: flex; align-items: center; gap: 8px; font-size: 12.5px; line-height: 1.6; }
  .contacts svg { width: 12px; height: 12px; flex: none; }
  /* Back */
  .card-back {
    left: 580px; top: 580px;
    background: linear-gradient(135deg, var(--blue-dark), var(--blue-light) 55%, var(--blue-mid));
    display: flex; align-items: center; justify-content: center;
  }
  .card-back .brand-lockup { gap: 14px; }
  .card-back .brand-mark { width: 16px; height: 16px; background: var(--white); }
  .card-back .brand-name { color: var(--white); font-size: 28px; letter-spacing: 5px; }
</style>
</head>
<body>

<section class="card card-front" aria-label="Business card front">
  <svg class="front-panel" viewBox="0 0 560 320" preserveAspectRatio="none" aria-hidden="true">
    <defs>
      <linearGradient id="panelBlue" x1="0" y1="0" x2="1" y2="1">
        <stop offset="0" stop-color="#5e94bf"/>
        <stop offset="1" stop-color="#3d6b92"/>
      </linearGradient>
    </defs>
    <path d="M270 0 H560 V320 H270 V80 L258 70 L270 60 Z" fill="url(#panelBlue)"/>
  </svg>

  <div class="brand-lockup">
    <span class="brand-mark"></span>
    <span class="brand-name">Quorin<br>Investments</span>
  </div>

  <div class="details">
    <p class="holder-name">Yusuf K Bin Tarrah</p>
    <p class="holder-title">Managing Director</p>
    <p class="company">Quorin Investments</p>
    <p class="address">Harbor district, palwick tower,<br>office 2212, dubai</p>
    <ul class="contacts">
      <li>
        <svg viewBox="0 0 12 12" aria-hidden="true"><path d="M2 1h3l1 3-1.5 1a6 6 0 0 0 2.5 2.5L8 6l3 1v3a1 1 0 0 1-1 1A9 9 0 0 1 1 2a1 1 0 0 1 1-1z" fill="#fff"/></svg>
        tel. 04 3850927
      </li>
      <li>
        <svg viewBox="0 0 12 12" aria-hidden="true"><rect x="3" y="0.5" width="6" height="11" rx="1" fill="none" stroke="#fff"/><circle cx="6" cy="9.5" r="0.7" fill="#fff"/></svg>
        mobile. 050 9184203
      </li>
      <li>
        <svg viewBox="0 0 12 12" aria-hidden="true"><rect x="0.5" y="2.5" width="11" height="7" fill="none" stroke="#fff"/><path d="M0.5 2.5 6 7l5.5-4.5" fill="none" stroke="#fff"/></svg>
        yusuf@quorin-mail.ae
      </li>
      <li>
        <svg viewBox="0 0 12 12" aria-hidden="true"><circle cx="6" cy="6" r="5.2" fill="none" stroke="#fff"/><path d="M0.8 6h10.4M6 0.8c-3 3-3 7.4 0 10.4M6 0.8c3 3 3 7.4 0 10.4" fill="none" stroke="#fff" stroke-width="0.8"/></svg>
        www.quorin-mail.ae
      </li>
    </ul>
  </div>
</section>

<section class="card card-back" aria-label="Business card back">
  <div class="brand-lockup">
    <span class="brand-mark"></span>
    <span class="brand-name">Quorin Investments</span>
  </div>
</section>

</body>
</html>
```